4D Cradle Glimpse Luxury Ultrasound Billboard

Design a HIGH-END, MODERN billboard for my private prenatal ultrasound studio, 4D Cradle Glimpse, located in Pace, Florida.
This billboard will be viewed by drivers traveling at highway speeds, so it must be extremely clean, simple, and readable within 6 seconds.
About My Business
4D Cradle Glimpse is a private prenatal ultrasound studio specializing in:
Highest technology 4D/HD Ultrasounds
Early Gender Determination
Pregnancy Confirmation
I have been serving families for nearly 10 years and is known for creating a memorable experience, not just an ultrasound appointment.
Design Style
I DO NOT want:
Flowers
Leaves
Swirls
Glitter
Hearts everywhere
Busy backgrounds
Generic maternity stock graphics
I DO want:
Modern
Luxury
Upscale
Clean
Professional
Eye-catching
Premium medical spa feel
Colors
Use colors from my logo:
LOGO Green ( or a deep green)
Black
White
Soft Gold accents
Images:
Incorporate my professional headshot in a clean, modern way, logo, and the ultrasound images
Text
Keep wording minimal.
Primary Headline ( OPEN TO IDEAS) :
EXAMPLES ( WOULD RATHER SOMETHING MORE CATCHY)
" ADVANCED IMAGING. UNFORGETTABLE MOMENTS"
"MEET YOUR BABY BEFORE BIRTH"
Under headline:
4D Ultrasound • Early Gender • Pregnancy Confirmation
Business Name:
4D Cradle Glimpse
Private Prenatal Ultrasound Studio
Phone Number:
850-471-5923
Important
This billboard must be readable in 5–6 seconds from a moving vehicle.
Less text is better.
The phone number and business name must be visible from a distance.
The design should feel like a premium brand that immediately tells expecting parents:
“This is where I go to see my baby.”
Files Provided
Official logo
Headshot
Ultrasound images
Don’t make this look like a medical office billboard.
Make it look like a luxury baby experience billboard. That’s what separates 4D Cradle Glimpse from hospitals, OB offices, and all the new studios popping up around you. The emotional connection is what gets moms to book. ❤️
Billboard Size - 10.6” x 36”

```html
<!DOCTYPE html>
<html lang="en">
<head>
<meta charset="utf-8">
<title>4D Cradle Glimpse Billboard</title>
<link rel="stylesheet" href="https://fonts.googleapis.com/css2?family=Saira+Semi+Condensed:wght@700;800&display=swap">
<style>
  :root {
    --slate-green: #5d6a63;
    --slate-green-dark: #4f5b55;
    --gold: #c99c3a;
    --white: #ffffff;
    --ink: #2b2b2b;
  }
  * { margin: 0; padding: 0; box-sizing: border-box; }
  html, body { width: 1200px; height: 730px; overflow: hidden; background: #e9ecea; }
  .billboard {
    position: relative;
    width: 1200px;
    height: 730px;
    overflow: hidden;
    background: linear-gradient(90deg, #f1f1f1 0%, var(--white) 30%);
    font-family: "Saira Semi Condensed", "Arial Narrow", sans-serif;
  }
  .headshot {
    position: absolute;
    left: 0; top: 30px;
    width: 260px; height: 610px;
    background: linear-gradient(180deg, #d9c9a4 0%, #c7b08a 35%, #3e4a43 75%, #2f3833 100%);
  }
  .ultrasound-portrait {
    position: absolute;
    left: 950px; top: -90px;
    width: 460px; height: 460px;
    border-radius: 50%;
    border: 4px solid var(--gold);
    background: radial-gradient(circle at 40% 50%, #b3604a 0%, #8a3b2c 45%, #3a1712 85%);
  }
  .bands { position: absolute; inset: 0; }
  .headline {
    position: absolute;
    left: 272px; top: 44px;
    width: 660px;
    color: var(--slate-green);
    font-weight: 800;
    font-size: 66px;
    line-height: 1.02;
    letter-spacing: 1px;
    text-transform: uppercase;
    white-space: nowrap;
  }
  .headline .line-two { display: block; padding-left: 34px; }
  .services {
    position: absolute;
    left: 274px; top: 222px;
    color: var(--gold);
    font-weight: 800;
    font-size: 36px;
    line-height: 1.25;
    white-space: nowrap;
  }
  .services .line-two { display: block; padding-left: 8px; }
  .phone {
    position: absolute;
    left: 30px; top: 605px;
    display: flex;
    align-items: center;
    gap: 20px;
  }
  .phone-icon { width: 62px; height: 62px; flex: none; }
  .phone-number {
    color: var(--white);
    font-weight: 800;
    font-size: 92px;
    line-height: 1;
    letter-spacing: 1px;
    white-space: nowrap;
  }
  .brand-panel {
    position: absolute;
    left: 805px; top: 430px;
    width: 360px; height: 270px;
    background: var(--white);
    padding: 18px;
  }
  .brand-frame {
    width: 100%; height: 100%;
    border: 4px solid var(--slate-green);
    border-radius: 22px;
    display: flex;
    flex-direction: column;
    align-items: center;
    justify-content: center;
    text-align: center;
  }
  .brand-name {
    color: var(--gold);
    font-weight: 800;
    font-size: 46px;
    line-height: 1.02;
  }
  .brand-rule {
    width: 82%;
    height: 2px;
    background: var(--gold);
    margin: 14px 0 10px;
  }
  .brand-tagline {
    color: var(--slate-green);
    font-weight: 700;
    font-size: 16px;
    letter-spacing: 1px;
    text-transform: uppercase;
    white-space: nowrap;
  }
</style>
</head>
<body>
  <div class="billboard">
    <div class="headshot" role="img" aria-label="Professional headshot of the studio owner"></div>
    <div class="ultrasound-portrait" role="img" aria-label="4D ultrasound image of twin babies"></div>

    <svg class="bands" viewBox="0 0 1200 730" aria-hidden="true">
      <path d="M0 596 C 400 530, 800 395, 1200 322 L1200 352 C 800 425, 400 560, 0 626 Z" fill="var(--gold)"/>
      <path d="M0 624 C 400 558, 800 423, 1200 350 L1200 730 L0 730 Z" fill="var(--slate-green)"/>
    </svg>

    <h1 class="headline">Meet your baby<span class="line-two">before birth</span></h1>

    <p class="services">4D Ultrasound &bull; Early Gender<span class="line-two">&bull; Pregnancy Confirmation</span></p>

    <div class="phone">
      <svg class="phone-icon" viewBox="0 0 64 64" aria-hidden="true">
        <circle cx="32" cy="32" r="30" fill="var(--gold)" stroke="var(--ink)" stroke-width="2"/>
        <path d="M23 16c2-1 4 0 5 2l3 6c1 2 0 3-1 4l-2 2c1 4 4 8 8 10l2-2c1-1 3-2 4-1l6 3c2 1 3 3 2 5l-2 3c-1 2-4 3-7 2-11-4-19-12-22-23-1-3 0-6 2-7z" fill="var(--ink)"/>
      </svg>
      <span class="phone-number">850-471-5923</span>
    </div>

    <div class="brand-panel">
      <div class="brand-frame">
        <div class="brand-name">4D Cradle<br>Glimpse</div>
        <div class="brand-rule"></div>
        <div class="brand-tagline">Prenatal Ultrasound Studio</div>
      </div>
    </div>
  </div>
</body>
</html>
```